Maple Roster Business Card for recruitment company

We are looking for a Business Card Design that incorporates our personal details and our busines name and logo. We are a specialized search consultancy that recruit Property and Construction professionals.
We would like a business card that stands out and is appealing to the Construction and Property industry as well.

Target Market(s)

people in the construction and property industry

Contact Information for Business Card

Business Name and logo

Font styles to use
Serif

Colors
0094D4
00A9DD
6FCCEA
C7EBF8
E9F6FB

Requirements
Must have
• Business name and logo as well as contact details
Should not have
• No photos of us please

```html
<!DOCTYPE html>
<html lang="en">
<head>
<meta charset="utf-8">
<title>Maple Roster – Business Card</title>
<link rel="stylesheet" href="https://fonts.googleapis.com/css2?family=Montserrat:wght@300;400;600&display=swap">
<style>
  :root {
    --teal-deep: #0e4257;
    --ink-grey: #5b5f63;
    --card-white: #ffffff;
    --backdrop: #dedede;
    --backdrop-light: #ececec;
  }
  * { margin: 0; padding: 0; box-sizing: border-box; }
  html, body { width: 900px; height: 1200px; overflow: hidden; }
  body {
    background: radial-gradient(circle at 50% 50%, var(--backdrop-light), var(--backdrop));
    font-family: "Montserrat", Arial, sans-serif;
    position: relative;
  }
  .card {
    position: absolute;
    left: 80px;
    width: 740px;
    height: 450px;
    box-shadow: 0 4px 14px rgba(0,0,0,0.18);
  }
  .card-front {
    top: 138px;
    background: var(--card-white);
    border-bottom: 12px solid var(--teal-deep);
  }
  .card-back {
    top: 632px;
    background: var(--teal-deep);
  }
  .wordmark {
    position: absolute;
    font-weight: 300;
    letter-spacing: 0.06em;
    text-transform: uppercase;
    white-space: nowrap;
  }
  .card-front .wordmark {
    left: 55px;
    top: 196px;
    font-size: 35px;
    color: var(--teal-deep);
  }
  .card-back .wordmark {
    left: 0; right: 0;
    top: 190px;
    text-align: center;
    font-size: 50px;
    color: var(--card-white);
  }
  .divider {
    position: absolute;
    left: 420px;
    top: 87px;
    width: 1.5px;
    height: 330px;
    background: var(--teal-deep);
    opacity: 0.6;
  }
  .contact-block {
    position: absolute;
    left: 452px;
    top: 112px;
    color: var(--ink-grey);
  }
  .person-name {
    font-size: 24px;
    font-weight: 600;
    color: var(--teal-deep);
    line-height: 1.1;
  }
  .person-role {
    font-size: 14px;
    margin-top: 4px;
  }
  .contact-list {
    list-style: none;
    margin-top: 20px;
  }
  .contact-list li {
    display: flex;
    align-items: center;
    gap: 12px;
    font-size: 15px;
    line-height: 28px;
  }
  .contact-list svg { width: 14px; height: 14px; fill: var(--teal-deep); flex: none; }
  .address {
    margin-top: 26px;
    font-size: 15px;
    line-height: 24px;
  }
</style>
</head>
<body>
  <section class="card card-front">
    <div class="wordmark">Maple Roster</div>
    <div class="divider"></div>
    <div class="contact-block">
      <div class="person-name">Lena Marsh</div>
      <div class="person-role">Owner/ Designer</div>
      <ul class="contact-list">
        <li>
          <svg viewBox="0 0 16 16" aria-hidden="true"><path d="M3 1h3l1.5 4-2 1.2a9 9 0 0 0 4.3 4.3L11 8.5l4 1.5v3a2 2 0 0 1-2 2A12 12 0 0 1 1 3a2 2 0 0 1 2-2z"/></svg>
          (555) 014-2290
        </li>
        <li>
          <svg viewBox="0 0 16 16" aria-hidden="true"><path d="M1 3h14v10H1z" opacity="0.9"/><path d="M1 3l7 6 7-6" fill="none" stroke="#fff" stroke-width="1.4"/></svg>
          info@mapleroster.com
        </li>
        <li>
          <svg viewBox="0 0 16 16" aria-hidden="true"><circle cx="8" cy="8" r="7"/><path d="M1 8h14M8 1c3 3 3 11 0 14M8 1c-3 3-3 11 0 14" fill="none" stroke="#fff" stroke-width="1"/></svg>
          www.mapleroster.com
        </li>
      </ul>
      <p class="address">82 Harbor Lane<br>Westbrook, CA 90000</p>
    </div>
  </section>

  <section class="card card-back">
    <div class="wordmark">Maple Roster</div>
  </section>
</body>
</html>
```